Beef cattle farm needs signs which can be seen from roadside

We would like submissions of artwork for a sign that will hang from a fence or gate and will be seen by passing cars.

Existing logo and branding theme for the company is attached.

Signage can be between 900mm x 400mm - 1200mm x 600mm

Industry/Entity Type

Farm

Requirements
Must have
• the Signs should have the following information:
• Company name: Wendlow Grazing Company
• Address: 417 Corrigan Flat Road
• Contact number: 0431 862 407
• email address: admin@wendlowgrazingcompany.com.au
• - Logo and branding as per attached artwork

```html
<!DOCTYPE html>
<html lang="en">
<head>
<meta charset="utf-8">
<title>Wendlow Grazing Company – Roadside Sign</title>
<link rel="stylesheet" href="https://fonts.googleapis.com/css2?family=Montserrat:wght@500&family=Arimo:wght@400;700&display=swap">
<style>
  :root {
    --backdrop: #858583;
    --paper: #ffffff;
    --brand-green: #0a5a30;
    --brand-green-deep: #064a27;
    --divider-light: #e4e4e4;
    --divider-dark: #9a9a9a;
    --type-light: #ffffff;
  }
  * { margin: 0; padding: 0; box-sizing: border-box; }
  html, body {
    width: 1200px;
    height: 655px;
    overflow: hidden;
    background: var(--backdrop);
  }
  .sign {
    position: absolute;
    left: 109px;
    top: 109px;
    width: 981px;
    height: 436px;
    background: var(--paper);
    overflow: hidden;
  }
  .sign__shapes {
    position: absolute;
    inset: 0;
  }
  .brand {
    position: absolute;
    left: 40px;
    top: 48px;
    width: 400px;
    text-align: center;
    color: var(--brand-green);
    font-family: "Montserrat", sans-serif;
    font-weight: 500;
  }
  .brand__mark {
    display: block;
    width: 190px;
    height: 190px;
    margin: 0 auto 28px;
    border-radius: 50%;
    background: var(--brand-green);
  }
  .brand__name {
    display: block;
    line-height: 1;
  }
  .brand__name--main {
    font-size: 60px;
    letter-spacing: 2px;
  }
  .brand__name--sub {
    margin-top: 10px;
    font-size: 25px;
    letter-spacing: 1px;
  }
  .contact {
    position: absolute;
    right: 33px;
    color: var(--type-light);
    font-family: "Arimo", Arial, sans-serif;
    text-align: right;
    white-space: nowrap;
  }
  .contact--phone {
    top: 46px;
    font-size: 33px;
    font-weight: 700;
  }
  .contact--details {
    bottom: 40px;
    line-height: 36px;
  }
  .contact__address {
    font-size: 23px;
    font-weight: 400;
  }
  .contact__email {
    font-size: 20px;
    font-weight: 700;
  }
</style>
</head>
<body>
  <main class="sign">
    <svg class="sign__shapes" width="981" height="436" viewBox="0 0 981 436" aria-hidden="false">
      <defs>
        <linearGradient id="divider-shade" x1="0" y1="0" x2="1" y2="0">
          <stop offset="0" stop-color="var(--divider-light)"/>
          <stop offset="1" stop-color="var(--divider-dark)"/>
        </linearGradient>
        <linearGradient id="grass-field" x1="0" y1="0" x2="1" y2="1">
          <stop offset="0" stop-color="#0b5b31"/>
          <stop offset="0.5" stop-color="#0d6136"/>
          <stop offset="1" stop-color="#08522b"/>
        </linearGradient>
      </defs>
      <path class="sign__divider" d="M430,0 Q596,218 430,436 L981,436 L981,0 Z" fill="url(#divider-shade)"/>
      <path class="sign__panel" d="M446,0 Q610,218 446,436 L981,436 L981,0 Z" fill="url(#grass-field)"
            role="img" aria-label="Faint grass blade pattern across the green panel"/>
    </svg>

    <div class="brand" aria-label="Wendlow Grazing Company">
      <span class="brand__mark"></span>
      <span class="brand__name brand__name--main">WENDLOW</span>
      <span class="brand__name brand__name--sub">GRAZING COMPANY</span>
    </div>

    <p class="contact contact--phone">Call : 0431 862 407</p>

    <div class="contact contact--details">
      <p class="contact__address">417 Corrigan Flat Road</p>
      <p class="contact__email">admin@wendlowgrazingcompany.com.au</p>
    </div>
  </main>
</body>
</html>
```